Vernac Law Business cards and stationary design project

We are looking for a stationary design for business cards (double sided), 8x10, 5x7, and legal and standard envelopes.

We would like the design to match the logo that we have already.
Color palate preferred is Teal, White, grey and any others that will look good for a professional law firm.

We would like this statement: "INTEGRITY. DILIGENCE. OUTCOMES" to be on the back of the business cards and maybe on the stationary if it looks good.

Please see link to website for more information: www.vernac-law.example

Target Market(s)

Potential clients that need Attorney services.

Industry/Entity Type

Law Firm

Contact Information for Business Card

We would like the front and back to be two different colors. Current business cards are teal front, grey back and are a vertical design. We are open to options with colors.

Font styles to use
Serif

Colors
33a6d7
33b8a4
b9b9b9
5c5c5c

Requirements
Must have
• Logo supplied needs to go on the card and stationary.
• Match website color palate, www.vernac-law.example
• Be professional and not too wordy.
• Criminal Law, Civil Litigation, Personal Injury, Restraining Orders need to be on the card.
Nice to have
• RELATIONSHIPS. RESPECT. RESULTS. on the back of the card.
Should not have
• Not be too busy/wordy or too flashy.

```html
<!DOCTYPE html>
<html lang="en">
<head>
<meta charset="utf-8">
<title>Vernac Law — Business Card</title>
<link href="https://fonts.googleapis.com/css2?family=Source+Sans+3:wght@400;600;700&display=swap" rel="stylesheet">
<style>
  :root {
    --stage: #000000;
    --card-white: #ffffff;
    --teal: #12889a;
    --ink: #111111;
    --type: "Source Sans 3", "Myriad Pro", Arial, sans-serif;
  }
  * { margin: 0; padding: 0; box-sizing: border-box; }
  html, body { width: 1200px; height: 900px; overflow: hidden; background: var(--stage); }
  .canvas { position: relative; width: 1200px; height: 900px; font-family: var(--type); }

  .card { position: absolute; top: 275px; width: 477px; height: 293px; overflow: hidden; }
  .card-front { left: 116px; background: var(--card-white); border-radius: 0 56px 0 56px; }
  .card-back  { left: 622px; background: var(--teal); border-radius: 56px 0 56px 0; }

  .brand-name { position: absolute; font-weight: 600; letter-spacing: 0.04em; white-space: nowrap; line-height: 1; }
  .card-front .brand-name { left: 0; width: 282px; top: 154px; text-align: center; font-size: 34px; color: var(--teal); }
  .card-back .brand-name { left: 0; width: 477px; top: 117px; text-align: center; font-size: 32px; color: var(--card-white); }

  .holder { position: absolute; right: 19px; top: 34px; text-align: right; }
  .holder-name { font-size: 20px; font-weight: 700; color: var(--teal); line-height: 24px; }
  .holder-title { font-size: 13.5px; color: var(--ink); line-height: 18px; }

  .address { position: absolute; right: 20px; top: 139px; text-align: right; font-size: 13.5px; line-height: 17px; color: var(--ink); }

  .contacts { position: absolute; right: 19px; top: 192px; list-style: none; font-size: 13.5px; color: var(--ink); }
  .contacts li { display: flex; justify-content: flex-end; align-items: center; gap: 6px; height: 18px; }
  .contacts svg { width: 11px; height: 11px; fill: var(--teal); }

  .practice-areas { position: absolute; left: 0; width: 477px; top: 198px; text-align: center; color: var(--card-white); font-size: 13.5px; font-weight: 600; line-height: 17px; }
  .motto-band { position: absolute; left: 0; bottom: 0; width: 477px; height: 50px; background: var(--card-white); display: flex; align-items: center; justify-content: center; }
  .motto { color: var(--teal); font-size: 13.5px; font-weight: 700; letter-spacing: 0.01em; }
</style>
</head>
<body>
<div class="canvas">

  <section class="card card-front">
    <div class="brand-name">VERNAC LAW</div>

    <div class="holder">
      <div class="holder-name">Daniel Mercer</div>
      <div class="holder-title">Managing Director</div>
    </div>

    <div class="address">
      12345, Address Goes Here<br>
      Country Name, 123456
    </div>

    <ul class="contacts">
      <li>123.456.7890
        <svg viewBox="0 0 12 12"><path d="M1 4.5C1 3 3 2 6 2s5 1 5 2.5v1H8.5V4.2C7.8 4 6.9 3.9 6 3.9S4.2 4 3.5 4.2v1.3H1z"/><rect x="3" y="6" width="6" height="4" rx="1"/></svg>
      </li>
      <li>123.456.7890
        <svg viewBox="0 0 12 12"><rect x="1.5" y="4" width="9" height="6.5" rx="1"/><rect x="3.5" y="1.5" width="5" height="3" fill="#fff" stroke="#12889a" stroke-width="1"/></svg>
      </li>
      <li>info@youremail.com
        <svg viewBox="0 0 12 12"><rect x="1" y="3" width="10" height="7"/><path d="M1 3l5 4 5-4" fill="none" stroke="#fff" stroke-width="1"/></svg>
      </li>
      <li>www.website.com
        <svg viewBox="0 0 12 12"><path d="M4.5 9.5l-1 1a2 2 0 0 1-2.8-2.8l2-2a2 2 0 0 1 2.8 0M7.5 2.5l1-1a2 2 0 0 1 2.8 2.8l-2 2a2 2 0 0 1-2.8 0M4 8l4-4" fill="none" stroke="#12889a" stroke-width="1.3"/></svg>
      </li>
    </ul>
  </section>

  <section class="card card-back">
    <div class="brand-name">VERNAC LAW</div>
    <p class="practice-areas">
      Practice areas, Criminal Law<br>
      Civil Litigation/Personal Injury, Restraining Orders
    </p>
    <div class="motto-band">
      <span class="motto">INTEGRITY. DILIGENCE. OUTCOMES</span>
    </div>
  </section>

</div>
</body>
</html>
```